KTWG application splash screen

We need a 1024x768 image for use as an application splash screen.
The image will be displayed full screen on an 10 inch industrial PC 1024x768 screen while our application is launching. The image should convey that the application is "Waiting for connection to Wi-Fi access point..." and include a graphic of the industrial PC connected to the access point via an Ethernet cable. A list of troubleshooting steps should be included at the bottom of the image. The troubleshooting steps should not be the main focus of the image and should be shown in a smaller font (but still readable at 1024x768 displayed on a 10 inch screen).
I will include a mock up of the general idea of what we are looking for as well as image files for the industrial PC, a screenshot of our application to show on the PC's screen and the AP.
For general look and feel and a sense of corporate branding please review our website https://marrowgatesoilworks.example/. The splash screen should reflect corporate branding.
Target Market(s)
Users of our application
Industry/Entity Type
Agriculture
Look and feel

```html
<!DOCTYPE html>
<html lang="en">
<head>
<meta charset="utf-8">
<title>KTWG – Waiting for Wi-Fi access point</title>
<link rel="stylesheet" href="https://fonts.googleapis.com/css2?family=Barlow:wght@400;500;600&family=Open+Sans:wght@400;500&display=swap">
<style>
  :root {
    --brand-green: #2cb573;
    --paper: #ffffff;
    --ink-dark: #1a1a1a;
    --cable: #1c1c1c;
    --device-shell: #232323;
    --device-screen: #dfe5e2;
    --ap-light: #f4f5f5;
    --ap-shade: #d9dcdc;
  }
  * { margin: 0; padding: 0; box-sizing: border-box; }
  html, body { width: 1200px; height: 900px; overflow: hidden; background: var(--paper); }
  .splash {
    position: relative;
    width: 1200px;
    height: 900px;
    overflow: hidden;
    background: var(--paper);
    font-family: "Barlow", sans-serif;
  }
  .backdrop { position: absolute; inset: 0; }
  .headline {
    position: absolute;
    left: 60px;
    top: 30px;
    width: 690px;
    text-align: center;
    color: var(--paper);
    font-family: "Barlow", sans-serif;
    font-weight: 500;
    font-size: 80px;
    line-height: 84px;
    letter-spacing: 0.5px;
  }
  .cab-computer {
    position: absolute;
    left: 91px;
    top: 387px;
    width: 317px;
    height: 234px;
    border-radius: 14px;
    background: var(--device-shell);
  }
  .cab-computer .screen {
    position: absolute;
    left: 26px;
    top: 22px;
    right: 26px;
    bottom: 30px;
    border-radius: 3px;
    background: linear-gradient(180deg, var(--device-screen), #c9d6cf);
  }
  .cab-label {
    position: absolute;
    left: 91px;
    top: 646px;
    width: 317px;
    text-align: center;
    color: var(--brand-green);
    font-size: 22px;
    font-weight: 500;
  }
  .access-point {
    position: absolute;
    left: 1002px;
    top: 141px;
    width: 74px;
    height: 392px;
    border-radius: 10px 10px 16px 16px;
    background: linear-gradient(90deg, var(--ap-shade), var(--ap-light) 45%, var(--ap-shade));
  }
  .ap-label {
    position: absolute;
    left: 944px;
    top: 614px;
    width: 181px;
    text-align: center;
    color: var(--paper);
    font-size: 20px;
    font-weight: 600;
    line-height: 24px;
    letter-spacing: 0.3px;
  }
  .brand-badge {
    position: absolute;
    left: 947px;
    top: 701px;
    width: 172px;
    height: 172px;
    border-radius: 42px;
    background: var(--brand-green);
    display: flex;
    align-items: center;
    justify-content: center;
    color: var(--paper);
    font-family: "Barlow", sans-serif;
    font-weight: 600;
    font-size: 44px;
    letter-spacing: 1px;
  }
  .troubleshooting {
    position: absolute;
    left: 64px;
    top: 714px;
    width: 840px;
    color: var(--paper);
    font-family: "Open Sans", sans-serif;
    font-size: 14px;
    line-height: 18.5px;
  }
  .troubleshooting h2 {
    font-size: 14.5px;
    font-weight: 500;
    margin-bottom: 10px;
  }
  .troubleshooting ul { list-style: none; }
  .steps > li {
    position: relative;
    padding-left: 20px;
  }
  .steps > li::before {
    content: "➤";
    position: absolute;
    left: 0;
    top: 0;
    font-size: 14px;
  }
  .sub-steps > li {
    position: relative;
    padding-left: 18px;
  }
  .sub-steps > li::before {
    content: "➡";
    position: absolute;
    left: 0;
    top: 0;
    font-size: 12px;
  }
</style>
</head>
<body>
<main class="splash">
  <svg class="backdrop" width="1200" height="900" viewBox="0 0 1200 900" aria-hidden="true">
    <path class="top-wave" fill="var(--brand-green)"
      d="M0 0 H1200 V120 H950 C845 120 812 175 775 240 C748 288 716 314 660 314 H0 Z"/>
    <path class="ap-column" fill="var(--brand-green)"
      d="M944 900 V170 Q944 123 991 123 H1078 Q1125 123 1125 170 V900 Z"/>
    <rect class="bottom-band" fill="var(--brand-green)" x="0" y="697" width="1200" height="203"/>
    <rect class="badge-frame" fill="var(--paper)" x="926" y="677" width="217" height="260" rx="46"/>
    <path class="ethernet-cable" fill="none" stroke="var(--cable)" stroke-width="5" stroke-linecap="round"
      d="M408 586 H1005 Q1037 586 1037 555 V530"/>
  </svg>

  <h1 class="headline">Waiting for connection to Wi-Fi access point...</h1>

  <div class="cab-computer" role="img" aria-label="Rugged tractor cab computer displaying the KTWG seeding application">
    <div class="screen"></div>
  </div>
  <p class="cab-label">Tractor Cab Computer</p>

  <div class="access-point" role="img" aria-label="White outdoor Wi-Fi access point with two antennas"></div>
  <p class="ap-label">Wi-Fi Access<br>Point</p>

  <div class="brand-badge">KTWG</div>

  <section class="troubleshooting">
    <h2>Troubleshooting steps:</h2>
    <ul class="steps">
      <li>This screen should only be visible for a short time on boot.</li>
      <li>If this screen stays visible for more than a minute:
        <ul class="sub-steps">
          <li>Verify that the Wi-Fi Access Point (AP) powers up when this system does (indicated by a green light on the side of the AP).</li>
          <li>Check the Ethernet cable between this system and the AP for damage, and replace it if necessary.</li>
          <li>Power-cycle this system and wait for it to reboot fully.</li>
          <li>If the issue persists, contact KTWG support for further assistance.</li>
        </ul>
      </li>
    </ul>
  </section>
</main>
</body>
</html>
```